RV7 - Rapid Vigil Field Operations Suite

I need an introductory website for RV7 which describes the features of the product and the ease of use of the product. The product is focused on Preparing for an incident using Volunteer and Resource management and then responding to an incident with Incident Management, Team Management, Task Management and Communication Management. Once a situation is handled, the application provides complete reporting on each of the above aspects

Target Market(s)

Local Government entities, specifically the emergency department directors or coordinators

Industry/Entity Type

Government Office

Coding

Coded - Design and coding required

Font styles to use
Sans Serif

Requirements
Must have
• Clear layout with modern images. I want to be able to get a clear understanding of the features of the product and the ease of use. I would like to high light how the application helps in Communication Management, Team Management, Task Management and Incident Managements. Also, how the use of application helps to get an immediate snap shot of how well an incident was handled. I want to highlight how the Dashboard provides a quick look at the Incident(s) being managed
Nice to have
• I would like to in the future add videos to the site. At this point don't have any ideas about nice to have features
Should not have
• traditional designs. I am looking for a slick, modern looking website. Clean design is the key.

```html
<!DOCTYPE html>
<html lang="en">
<head>
<meta charset="utf-8">
<title>RV7 - Rapid Vigil Field Operations Suite</title>
<link href="https://fonts.googleapis.com/css2?family=Roboto+Condensed:wght@400;700&family=Roboto:ital,wght@0,400;0,500;0,700;1,400&display=swap" rel="stylesheet">
<style>
:root{
  --navy:#1d3f7f;
  --blue:#2a5aa8;
  --green:#6aa43a;
  --dark:#1b1c1f;
  --footer:#222429;
  --text:#555a61;
  --ink:#1a1a1a;
  --light:#f4f5f7;
  --white:#ffffff;
}
*{margin:0;padding:0;box-sizing:border-box}
html,body{width:1200px;height:2612px;overflow:hidden}
body{position:relative;font-family:Roboto,Arial,sans-serif;color:var(--text);background:var(--white)}
.abs{position:absolute}

.topbar{left:0;top:0;width:1200px;height:44px;background:var(--dark);color:#ddd;font-size:13px}
.social{left:98px;top:14px;display:flex;gap:10px}
.social span{width:10px;height:10px;border-radius:50%;background:#ddd;display:block}
.contact-top{right:98px;top:12px;display:flex;gap:34px}
.contact-top span{display:flex;align-items:center;gap:8px}

.hero{left:0;top:44px;width:1200px;height:592px;background:linear-gradient(100deg,#3d4248 0%,#6b7177 40%,#8c8a86 65%,#4b4f55 100%)}
.nav{left:99px;top:44px;width:1002px;height:81px;background:var(--white);border-radius:40px;box-shadow:0 2px 8px rgba(0,0,0,.15);z-index:2}
.brand{left:26px;top:18px;display:flex;align-items:center;gap:10px}
.brand .dot{width:44px;height:44px;border-radius:50%;background:var(--navy)}
.brand b{font-family:"Roboto Condensed",sans-serif;font-weight:700;font-size:30px;color:var(--navy)}
.menu{right:38px;top:0;display:flex;gap:40px;height:81px;align-items:center;font-size:14px;font-weight:500;color:#222}
.menu a{color:inherit;text-decoration:none;position:relative;height:81px;display:flex;align-items:center}
.menu a.active{color:var(--blue)}
.menu a.active::before{content:"";position:absolute;top:-1px;left:-10px;right:-10px;height:3px;background:var(--green)}
.hero-title{left:122px;top:314px;color:var(--white);font-family:"Roboto Condensed",sans-serif;text-shadow:0 2px 6px rgba(0,0,0,.4)}
.hero-title h1{font-size:48px;font-weight:700;line-height:1}
.hero-title p{font-size:31px;font-weight:700;margin-top:12px}
.chev{top:300px}

.sec-head{display:flex;align-items:center;justify-content:center;gap:14px;font-family:"Roboto Condensed",sans-serif;font-weight:700;font-size:29px;color:var(--navy);width:1200px;left:0}
.sec-head i{width:40px;height:40px;border:3px solid var(--navy);border-radius:4px;display:block}
.sec-head em{font-style:normal;color:var(--green)}
.intro{left:0;top:738px;width:1200px;text-align:center;font-size:13.5px;line-height:24px}

.card{top:819px;width:314px;height:231px;border-radius:8px;box-shadow:0 2px 8px rgba(0,0,0,.25);overflow:hidden}
.card .photo{position:absolute;inset:0}
.card .cap{position:absolute;left:0;right:0;bottom:0;height:62px;background:rgba(30,80,160,.92);color:var(--white);padding:12px 14px}
.card .cap b{font-family:"Roboto Condensed",sans-serif;font-size:16px;display:block}
.card .cap small{font-size:11px;opacity:.9}
.card.green .cap{background:none;height:80px}
.card.green .photo::after{content:"";position:absolute;left:0;bottom:0;width:100%;height:60%;background:rgba(106,164,58,.88);clip-path:polygon(0 30%,100% 70%,100% 100%,0 100%)}

.why{left:0;top:1094px;width:1200px;height:418px;background:var(--light);border-top:1px solid #ddd;border-bottom:1px solid #ddd}
.feat{top:1216px;width:240px;text-align:center}
.feat .ic{width:104px;height:104px;border-radius:50%;background:radial-gradient(circle at 40% 30%,#2f60b0,var(--navy));margin:0 auto;display:flex;align-items:center;justify-content:center}
.feat.on .ic{background:radial-gradient(circle at 40% 30%,#86be52,var(--green))}
.feat h3{font-family:"Roboto Condensed",sans-serif;font-size:18px;color:var(--ink);margin-top:24px}
.feat p{font-size:12.5px;line-height:22px;margin-top:8px}
.feat a{display:block;margin-top:12px;font-size:13px;font-weight:700;color:var(--navy);text-decoration:none}
.feat.on a{color:var(--green)}

.adopt-img{left:0;top:1512px;width:610px;height:373px;background:linear-gradient(110deg,#cfc8bd,#8d8172 50%,#4a4540);clip-path:polygon(0 0,100% 0,65% 100%,0 100%)}
.adopt-stripe{left:0;top:1512px;width:612px;height:373px;background:var(--green);clip-path:polygon(96% 0,100% 0,66% 100%,62% 100%)}
.adopt{left:650px;top:1560px;width:452px}
.adopt .sec-head{position:static;width:auto;justify-content:flex-start}
.adopt p{font-size:12.5px;line-height:22px;margin-top:14px}
.btn{display:inline-block;background:var(--navy);color:var(--white);font-size:13px;font-weight:500;padding:11px 18px;margin-top:30px;border-radius:2px}

.testi{left:0;top:1885px;width:1200px;height:359px;background:linear-gradient(90deg,#1f4e9a,#2b5fb0 50%,#1f4e9a);color:var(--white);text-align:center}
.testi .sec-head{color:var(--white);top:50px}
.testi .sec-head i{border-color:var(--white)}
.quote{left:567px;top:116px;width:42px;height:42px;border:2px solid var(--green);border-radius:50%}
.testi .txt{left:240px;top:180px;width:720px;font-style:italic;font-size:12.5px;line-height:24px}
.testi .by{left:0;width:1200px;top:266px;font-weight:700;font-size:15px;line-height:28px}
.arrow{top:164px;width:34px;height:34px;border:2px solid var(--white);border-radius:50%}

.footer{left:0;top:2244px;width:1200px;height:368px;background:var(--footer);color:var(--white)}
.fcol{top:54px}
.fcol .fi{height:22px;display:flex;align-items:center}
.fcol h4{font-size:17px;font-weight:500;margin-top:14px}
.fcol p{font-size:12.5px;line-height:22px;margin-top:8px;color:#e8e8e8}
.divider{left:98px;top:209px;width:1004px;height:1px;background:#3a3c42}
.fbrand{left:98px;top:250px}
.fbrand h4{font-size:21px;font-weight:500}
.fbrand p{font-size:11.5px;color:#aaa;margin-top:8px}
.fbrand .social{position:static;margin-top:10px}
.fbrand .social span{background:#aaa}
.subscribe{left:758px;top:250px}
.subscribe h4{font-size:21px;font-weight:500}
.field{margin-top:10px;display:flex;gap:7px}
.field span{width:282px;height:40px;background:#3a3b40;border:1px solid #555;font-size:12px;color:#bbb;padding:12px 14px}
.field b{width:54px;height:40px;background:var(--green);display:flex;align-items:center;justify-content:center;font-size:15px}
</style>
</head>
<body>

<header class="abs topbar">
  <div class="abs social"><span></span><span></span><span></span><span></span><span></span></div>
  <div class="abs contact-top">
    <span><svg width="12" height="12" viewBox="0 0 24 24"><path fill="#ddd" d="M6.6 10.8a15 15 0 006.6 6.6l2.2-2.2c.3-.3.7-.4 1-.2 1.1.4 2.3.6 3.6.6.6 0 1 .4 1 1V20c0 .6-.4 1-1 1A17 17 0 013 4c0-.6.4-1 1-1h3.5c.6 0 1 .4 1 1 0 1.3.2 2.5.6 3.6.1.3 0 .7-.2 1z"/></svg>+ 4410 2298 517</span>
    <span><svg width="14" height="11" viewBox="0 0 14 11"><rect x="0.75" y="0.75" width="12.5" height="9.5" fill="none" stroke="#ddd" stroke-width="1.5"/><path d="M1 1l6 5 6-5" fill="none" stroke="#ddd" stroke-width="1.5"/></svg>hello@rv7suite.example</span>
  </div>
</header>

<section class="abs hero" role="img" aria-label="Photo of two coordinators reviewing an incident on a laptop in an office"></section>
<nav class="abs nav">
  <div class="abs brand"><span class="dot"></span><b>RV7</b></div>
  <div class="abs menu">
    <a class="active">HOME</a><a>ABOUT US</a><a>SERVICES</a><a>PROCESS</a><a>WEB APPLICATION</a><a>CONTACT US</a>
  </div>
</nav>
<svg class="abs chev" style="left:32px" width="34" height="110" viewBox="0 0 34 110"><path d="M32 2L2 55l30 53" fill="none" stroke="rgba(255,255,255,.6)" stroke-width="2"/></svg>
<svg class="abs chev" style="left:1146px" width="34" height="110" viewBox="0 0 34 110"><path d="M2 2l30 53-30 53" fill="none" stroke="rgba(255,255,255,.6)" stroke-width="2"/></svg>
<div class="abs hero-title">
  <h1>WE ARE EMERGENCY</h1>
  <p>COMMAND, CONTROL &amp; CO-ORDINATION</p>
</div>

<h2 class="abs sec-head" style="top:680px"><i></i><span>WELCOME TO <em>RV7</em></span></h2>
<p class="abs intro">RV-7 offers a web based and mobile interface to assist the CERT Community.The roles from CERT teams<br>have been created to have access to either the web, mobile or both the interfaces</p>

<div class="abs card green" style="left:99px">
  <div class="photo" role="img" aria-label="Photo of an admin team meeting around a table" style="background:linear-gradient(135deg,#d9d4cc,#8f8478)"></div>
  <div class="cap"><b>ADMIN</b><small>Prepare volunteers, resources and roles long before an incident begins</small></div>
</div>
<div class="abs card" style="left:444px">
  <div class="photo" role="img" aria-label="Photo of a hand arranging wooden blocks with people symbols" style="background:linear-gradient(135deg,#f1ece4,#b89d74)"></div>
  <div class="cap"><b>INCIDENT COMMANDER</b><small>Run Incident Management from one Dashboard</small></div>
</div>
<div class="abs card" style="left:789px">
  <div class="photo" role="img" aria-label="Photo of a volunteer presenting at a whiteboard of sticky notes" style="background:linear-gradient(135deg,#eef0f2,#a9adb2)"></div>
  <div class="cap"><b>VOLUNTEERS</b><small>Receive tasks and updates on web or mobile</small></div>
</div>

<section class="abs why"></section>
<h2 class="abs sec-head" style="top:1140px"><i></i><span>WHY YOU <em>CHOOSE US</em></span></h2>

<div class="abs feat" style="left:92px">
  <div class="ic"><svg width="54" height="34" viewBox="0 0 54 34" fill="#fff"><circle cx="27" cy="9" r="7"/><path d="M14 33c0-9 6-14 13-14s13 5 13 14z"/><circle cx="12" cy="12" r="5"/><path d="M1 31c0-7 4-11 11-11 2 0 3 0 4 1-2 3-3 6-3 10z"/><circle cx="42" cy="12" r="5"/><path d="M53 31c0-7-4-11-11-11-2 0-3 0-4 1 2 3 3 6 3 10z"/></svg></div>
  <h3>TEAM MANAGEMENT</h3>
  <p>Build CERT teams from your volunteer roster, assign roles and see who is deployed or available.</p>
  <a>READ MORE</a>
</div>
<div class="abs feat" style="left:350px">
  <div class="ic"><svg width="40" height="46" viewBox="0 0 40 46"><rect x="3" y="6" width="30" height="38" rx="2" fill="none" stroke="#fff" stroke-width="3"/><rect x="11" y="2" width="14" height="7" rx="1" fill="#fff"/><path d="M9 20h10M9 28h8M9 36h12" stroke="#fff" stroke-width="3"/><path d="M24 34l12-14" stroke="#fff" stroke-width="4"/></svg></div>
  <h3>TASK MANAGEMENT</h3>
  <p>Create, assign and follow each task from dispatch to close, with status flowing back to command.</p>
  <a>READ MORE</a>
</div>
<div class="abs feat on" style="left:608px">
  <div class="ic"><svg width="50" height="44" viewBox="0 0 50 44"><ellipse cx="28" cy="18" rx="19" ry="15" fill="#fff"/><ellipse cx="16" cy="26" rx="12" ry="10" fill="none" stroke="#fff" stroke-width="3"/><path d="M8 34l-4 7 9-4z" fill="#fff"/></svg></div>
  <h3>COMMUNICATION</h3>
  <p>Send alerts and updates to every team on web or mobile, so all responders share one message.</p>
  <a>READ MORE</a>
</div>
<div class="abs feat" style="left:866px">
  <div class="ic"><svg width="46" height="46" viewBox="0 0 46 46" stroke="#fff" stroke-width="5" stroke-linecap="round"><path d="M8 8l30 30"/><path d="M38 8L8 38"/><circle cx="8" cy="8" r="4" fill="none" stroke-width="3"/><circle cx="38" cy="38" r="4" fill="none" stroke-width="3"/></svg></div>
  <h3>DAMAGE ASSESSMENT</h3>
  <p>Log damage from the field and watch it roll up into the incident record and final reports.</p>
  <a>READ MORE</a>
</div>

<div class="abs adopt-stripe"></div>
<div class="abs adopt-img" role="img" aria-label="Photo of a briefing with a hand holding a smartphone showing the app"></div>
<div class="abs adopt">
  <h2 class="sec-head"><i></i><span>WHY ADOPT <em>RV7</em></span></h2>
  <p>RV7 takes your department from preparing to responding. Volunteer and Resource management get you ready; Incident, Team, Task and Communication management keep the response on track. The Dashboard gives a quick look at every incident being managed, with teams, tasks and status at a glance.</p>
  <p style="margin-top:8px">Once the situation is handled, RV7 provides complete reporting on each of these areas, giving an immediate snapshot of how well the incident was handled.</p>
  <span class="btn">READ MORE</span>
</div>

<section class="abs testi">
  <h2 class="abs sec-head"><i></i><span>OUR CLIENT TESTIMONIAL</span></h2>
  <div class="abs quote"></div>
  <div class="abs arrow" style="left:34px"></div>
  <div class="abs arrow" style="left:1132px"></div>
  <p class="abs txt">The Dashboard gave our emergency department a clear view of every incident as it unfolded. Teams, tasks and messages stayed in one place on web and mobile, and the reports afterward showed exactly how well our response was handled, which made the review with our county leadership quick and simple.</p>
  <p class="abs by">By<br>Marla (Manager)</p>
</section>

<footer class="abs footer">
  <div class="abs fcol" style="left:98px">
    <div class="fi"><svg width="14" height="20" viewBox="0 0 14 20"><path d="M7 0a7 7 0 00-7 7c0 5 7 13 7 13s7-8 7-13a7 7 0 00-7-7zm0 10a3 3 0 110-6 3 3 0 010 6z" fill="#fff"/></svg></div>
    <h4>Address</h4><p>200 Latin words, combined with a handful<br>of model combined</p>
  </div>
  <div class="abs fcol" style="left:411px">
    <div class="fi"><svg width="20" height="20" viewBox="0 0 24 24"><path fill="#fff" d="M6.6 10.8a15 15 0 006.6 6.6l2.2-2.2c.3-.3.7-.4 1-.2 1.1.4 2.3.6 3.6.6.6 0 1 .4 1 1V20c0 .6-.4 1-1 1A17 17 0 013 4c0-.6.4-1 1-1h3.5c.6 0 1 .4 1 1 0 1.3.2 2.5.6 3.6.1.3 0 .7-.2 1z"/></svg></div>
    <h4>Call Us</h4><p>Mobile Number :+4410229851<br>Toll free : +1800 3362901147</p>
  </div>
  <div class="abs fcol" style="left:705px">
    <div class="fi"><svg width="24" height="18" viewBox="0 0 14 11"><rect x="0.75" y="0.75" width="12.5" height="9.5" fill="none" stroke="#fff" stroke-width="1.2"/><path d="M1 1l6 5 6-5" fill="none" stroke="#fff" stroke-width="1.2"/></svg></div>
    <h4>Email us</h4><p>ops@rv7suite.example<br>team@rv7suite.example</p>
  </div>
  <div class="abs fcol" style="left:941px">
    <div class="fi"><svg width="20" height="20" viewBox="0 0 20 20" fill="none" stroke="#fff" stroke-width="2.4" stroke-linecap="round"><path d="M10 1v8"/><path d="M5 4a8 8 0 1010 0"/></svg></div>
    <h4>Information To Help</h4><p>Privacy Policy<br>Site map</p>
  </div>
  <div class="abs divider"></div>
  <div class="abs fbrand">
    <h4>We Are RV7</h4>
    <p>Copyrights@2016Company name , All rights reserved</p>
    <div class="social"><span></span><span></span><span></span></div>
  </div>
  <div class="abs subscribe">
    <h4>Subscribe Newsletter</h4>
    <div class="field"><span>Enter E mail Address</span><b>GO</b></div>
  </div>
</footer>

</body>
</html>
```